Landing Page and Logo for Auto-Blogging Platform

I created a platform that allows users to start a blog for their business, hobby, charity, etc. I need a landing page where users can learn about the platform, benefits of consistent blogging, SEO value, plans/pricing, etc. The landing page needs to have multiple call to action buttons encouraging the visitor to register/sign up for a free trial.

In addition to the landing page, I need a page for users to establish the settings for their blog. This page should be a fairly simple form, intended for the user to enter a few details to set up their blog:
1. Name of Blog
2. Up to 10 topics and/or keywords the blog should focus on
3. Theme: Color-scheme and logo upload for blog.

I have attached the specifications of the platform's functionality so you can better understand how it works, plans/pricing, etc.

I also need a logo for the business. The name of the platform is PostNook.

Target Market(s)

Website owners, bloggers, business owners

Industry/Entity Type

Technology, Internet, web design

Coding

Coded - Design and coding required

Number of Pages Required

2 page

Colors
0054AA
0677BA
7BADD7
CADEEF
E8F1F8
0094D4
00A9DD
6FCCEA
C7EBF8
E9F6FB

Requirements
Must have
• Eye-catching design but fairly light on content (keep it simple and brief.)
Nice to have
• Eye-catching yet simple design, clean and easy to understand what we are offering.
Should not have
• Too much “wordy” and confusing content.

```html
<!DOCTYPE html>
<html lang="en">
<head>
<meta charset="UTF-8">
<title>PostNook – Auto-Blogging Platform</title>
<link href="https://fonts.googleapis.com/css2?family=Lato:wght@400;700;900&display=swap" rel="stylesheet">
<style>
:root{
  --blue:#0054AA;
  --blue-mid:#0677BA;
  --blue-soft:#7BADD7;
  --blue-pale:#CADEEF;
  --blue-mist:#E8F1F8;
  --ink:#1b1f27;
  --text:#555b66;
  --night:#0b111b;
  --night-2:#151c28;
  --white:#ffffff;
  --line:#e3e6ea;
}
*{box-sizing:border-box;margin:0;padding:0}
html,body{width:1200px;height:2704px;overflow:hidden}
body{font-family:'Lato',Arial,sans-serif;color:var(--ink);background:var(--white);position:relative}
.abs{position:absolute}
.btn{display:inline-block;background:var(--blue);color:var(--white);font-weight:700;font-size:15px;padding:11px 20px;border-radius:2px}
.btn-ghost{background:transparent;border:2px solid var(--white)}

/* hero */
.hero{position:absolute;left:0;top:0;width:1200px;height:540px}
.hero-photo{position:absolute;inset:0;background:linear-gradient(90deg,#05080e 0%,#0c1522 40%,#2a3a4e 65%,#4a5a6c 80%,#1a2230 100%)}
.logo{display:flex;align-items:center;gap:12px;color:var(--white);font-weight:900;font-size:26px}
.logo-mark{width:40px;height:40px;border:3px solid var(--white);border-radius:4px}
.nav{position:absolute;left:490px;top:38px;display:flex;gap:10px;align-items:center}
.nav a{color:var(--white);font-size:15px;font-weight:700;padding:7px 10px;text-decoration:none}
.nav a.active{border:1px solid var(--white)}
.hero-kicker{left:112px;top:196px;color:var(--white);font-size:26px;font-weight:700}
.hero-title{left:108px;top:228px;color:var(--white);font-size:74px;font-weight:900;letter-spacing:-1px}
.hero-desc{left:112px;top:330px;width:380px;color:#d6dbe3;font-size:14px;line-height:1.5}
.hero-cta{left:112px;top:400px;display:flex;gap:14px}

/* about */
.about-photo{left:110px;top:648px;width:446px;height:288px;background:linear-gradient(135deg,#c9c2b6,#8a7d6d 50%,#5a5048)}
.bracket{width:36px;height:36px;border:4px solid var(--ink)}
.heading{display:flex;align-items:center;gap:14px;font-size:42px;font-weight:700}
.heading::before{content:"";width:5px;height:44px;background:var(--blue)}
.heading span{color:var(--blue)}
.about-text{left:640px;top:712px;width:450px;color:var(--text);font-size:13px;line-height:1.6}
.about-text p+p{margin-top:12px}

/* methods */
.methods{left:0;top:1044px;width:1200px;height:566px}
.methods-photo{position:absolute;inset:0;background:linear-gradient(90deg,#0a0e15 0%,#141a24 45%,#3b2e28 72%,#6a4e3c 85%,#251d1a 100%)}
.method{position:absolute;left:116px;display:flex;align-items:center;gap:24px;color:var(--white);font-size:15px;font-weight:700;line-height:1.45}
.method-icon{width:52px;height:52px;background:var(--blue-pale);border:3px solid var(--blue-mid);display:flex;align-items:center;justify-content:center;flex:none}
.connector{position:absolute;left:141px;width:0;border-left:2px dashed var(--white)}

/* pricing */
.card{position:absolute;top:1780px;width:270px;height:452px;background:var(--white);border:1px solid var(--line);box-shadow:0 4px 14px rgba(0,0,0,.08);overflow:hidden;text-align:center}
.card-top{position:absolute;left:-40px;top:-140px;width:350px;height:300px;border-radius:50%;background:#f1f2f4}
.card-top.featured{background:var(--blue)}
.card-inner{position:relative;padding-top:34px}
.plan-name{font-size:18px;font-weight:700}
.plan-price{font-size:40px;font-weight:900;color:var(--blue);margin-top:4px}
.plan-price small{font-size:40px}
.plan-period{font-size:17px;margin-top:2px}
.features{list-style:none;text-align:left;margin:68px 0 0 26px}
.features li{display:flex;align-items:center;gap:10px;font-size:12px;color:var(--text);height:30px}
.tick{width:14px;height:14px;border-radius:50%;background:var(--blue);flex:none}
.select{position:absolute;left:50%;transform:translateX(-50%);bottom:26px;background:var(--blue-pale);color:var(--ink);font-size:12px;font-weight:700;padding:9px 16px}
.featured-card .plan-name,.featured-card .plan-price,.featured-card .plan-period{color:var(--white)}
.featured-card .select{background:var(--blue);color:var(--white)}

/* footer */
.footer{left:0;top:2322px;width:1200px;height:382px;background:linear-gradient(90deg,#06090e,#111823 55%,#1c2330)}
.f-col{position:absolute;top:78px;color:var(--white)}
.f-col h4{font-size:18px;font-weight:700;margin-bottom:12px}
.f-col li{list-style:none;font-size:13px;color:#d3d8df;line-height:2}
.subscribe{left:112px;top:300px}
.email-field{left:112px;top:2628px}
.social{display:flex;gap:8px}
.social i{width:22px;height:22px;background:var(--blue-mid);display:block}
.contact-row{display:flex;align-items:center;gap:12px;font-size:13px;color:#d3d8df;height:40px}
.contact-row i{width:22px;height:22px;border-radius:50%;background:var(--white);display:block}
</style>
</head>
<body>

<header class="hero">
  <div class="hero-photo" role="img" aria-label="Man in glasses working on a laptop in a dim office"></div>
  <div class="logo abs" style="left:112px;top:32px"><span class="logo-mark"></span>PostNook</div>
  <nav class="nav">
    <a class="active">Home</a><a>About Us</a><a>Methods</a><a>Pricing</a><a>Benefits</a>
  </nav>
  <a class="btn abs" style="left:972px;top:34px">Contact Us</a>
  <div class="hero-kicker abs">Welcome To</div>
  <h1 class="hero-title abs">PostNook</h1>
  <p class="hero-desc abs">Lorem ipsum dolor sit amet, consectetur adipiscing elit, sed do eiusmod tempor incididunt ut labore et dolore magna aliqua.</p>
  <div class="hero-cta abs"><a class="btn">Sign Up For a Free Trial</a><a class="btn btn-ghost">Register Now</a></div>
</header>

<section>
  <div class="bracket abs" style="left:96px;top:632px;border-right:0;border-bottom:0"></div>
  <div class="about-photo abs" role="img" aria-label="Two colleagues smiling at a laptop"></div>
  <div class="bracket abs" style="left:532px;top:912px;border-left:0;border-top:0"></div>
  <h2 class="heading abs" style="left:640px;top:630px">About The&nbsp;<span>Platform</span></h2>
  <div class="about-text abs">
    <p>The purpose of this platform is to allow anyone to start a blog and automate the process of creating content and posting it to the blog. Here is what the platform will consist of:</p>
    <p>Each plan is set up once and then posts go out on schedule. Topics, tone and timing stay in your hands while we handle writing and publishing.</p>
  </div>
  <a class="btn abs" style="left:640px;top:876px">Read More</a>
</section>

<section class="methods abs">
  <div class="methods-photo" role="img" aria-label="Woman typing on a laptop in a warm lit office"></div>
  <h2 class="heading abs" style="left:112px;top:62px;color:var(--white)">Our&nbsp;<span>Methods</span></h2>
  <div class="connector" style="top:206px;height:64px"></div>
  <div class="connector" style="top:326px;height:56px"></div>
  <div class="method" style="top:154px"><div class="method-icon"><svg width="26" height="22"><rect x="1" y="1" width="24" height="20" fill="none" stroke="#0054AA" stroke-width="2"/><path d="M1 8h24M1 14h24M9 1v20M17 1v20" stroke="#0054AA" stroke-width="1.5"/></svg></div>The user enters them into a table manually</div>
  <div class="method" style="top:274px"><div class="method-icon"><svg width="22" height="26"><path d="M2 1h12l6 6v18H2z" fill="none" stroke="#0054AA" stroke-width="2"/><path d="M6 13h10M6 18h10" stroke="#0054AA" stroke-width="2"/></svg></div>The user uploads a list of blog topics in CSV format</div>
  <div class="method" style="top:386px"><div class="method-icon"><svg width="26" height="26"><circle cx="13" cy="13" r="10" fill="none" stroke="#0054AA" stroke-width="2"/><path d="M8 13l4 4 6-8" fill="none" stroke="#0054AA" stroke-width="2"/></svg></div>AI can create the list of blog topics based on a prompt<br>such as: "Provide a list of 52 topics for a<br>handyman business's blog"</div>
  <a class="btn abs" style="left:112px;top:482px;background:var(--white);color:var(--ink)">Read More</a>
</section>

<section>
  <h2 class="heading abs" style="left:480px;top:1676px">Our&nbsp;<span>Pricing</span></h2>

  <div class="card" style="left:190px">
    <div class="card-top"></div>
    <div class="card-inner">
      <div class="plan-name">Base Plan</div>
      <div class="plan-price">$9.99<small>mo.</small></div>
      <div class="plan-period">Every Month</div>
      <ul class="features"><li><i class="tick"></i>1 blog post (up to 1,000 words)</li><li><i class="tick"></i>Lorem ipsum dolor sit amet,</li><li><i class="tick"></i>Lorem ipsum dolor sit amet,</li><li><i class="tick"></i>Lorem ipsum dolor sit amet,</li><li><i class="tick"></i>Lorem ipsum dolor sit amet,</li></ul>
    </div>
    <span class="select">Select Plan</span>
  </div>

  <div class="card featured-card" style="left:464px;top:1760px;height:492px;z-index:2;box-shadow:0 8px 24px rgba(0,0,0,.18)">
    <div class="card-top featured" style="top:-120px"></div>
    <div class="card-inner" style="padding-top:44px">
      <div class="plan-name">Premium Plan</div>
      <div class="plan-price">$14.99<small>/mo.</small></div>
      <div class="plan-period">Every Week</div>
      <ul class="features" style="margin-top:78px"><li><i class="tick"></i>1 blog post (up to 1,000 words)</li><li><i class="tick"></i>Lorem ipsum dolor sit amet,</li><li><i class="tick"></i>Lorem ipsum dolor sit amet,</li><li><i class="tick"></i>Lorem ipsum dolor sit amet,</li><li><i class="tick"></i>Lorem ipsum dolor sit amet,</li></ul>
    </div>
    <span class="select">Select Plan</span>
  </div>

  <div class="card" style="left:740px">
    <div class="card-top"></div>
    <div class="card-inner">
      <div class="plan-name">Ultimate Plan</div>
      <div class="plan-price">$24.99<small>/mo</small></div>
      <div class="plan-period">Per Day</div>
      <ul class="features"><li><i class="tick"></i>1 blog post (up to 1,000 words)</li><li><i class="tick"></i>Lorem ipsum dolor sit amet,</li><li><i class="tick"></i>Lorem ipsum dolor sit amet,</li><li><i class="tick"></i>Lorem ipsum dolor sit amet,</li><li><i class="tick"></i>Lorem ipsum dolor sit amet,</li></ul>
    </div>
    <span class="select">Select Plan</span>
  </div>
</section>

<footer class="footer abs">
  <div class="logo abs" style="left:112px;top:80px"><span class="logo-mark"></span>PostNook</div>
  <div class="abs" style="left:112px;top:186px;width:296px;height:48px;background:var(--white);color:#8a9099;font-size:13px;padding:15px 14px">Enter Email Address</div>
  <a class="btn abs" style="left:112px;top:252px;padding:9px 18px">Subscribe</a>

  <div class="f-col" style="left:506px"><h4>Quick Links</h4><ul><li>Home</li><li>About Us</li><li>Methods</li><li>Pricing</li><li>Benefits</li><li>Contact Us</li></ul></div>
  <div class="f-col" style="left:694px"><h4>Help Links</h4><ul><li>Privacy Policy</li><li>Terms &amp; Conditions</li><li>Disclaimer</li></ul>
    <h4 style="margin-top:20px">Follow Us</h4><div class="social"><i></i><i></i><i></i><i></i></div></div>
  <div class="f-col" style="left:892px"><h4>Contact Info</h4>
    <div class="contact-row"><i></i>Lorem Ipsum, Usa - 457556</div>
    <div class="contact-row"><i></i>+1 (000) 000 00000</div>
    <div class="contact-row"><i></i>hello@postnook.example</div>
  </div>
  <div class="abs" style="left:0;top:340px;width:1200px;border-top:1px solid rgba(255,255,255,.15)"></div>
  <div class="abs" style="left:0;top:352px;width:1200px;text-align:center;color:#c3c8d0;font-size:12px">© 2024. PostNook. All Rights reserved.</div>
</footer>

</body>
</html>
```